Logo and Card design for KRV Home Solutions LLC

I need an edgier logo and business card designs. Current logo attached. I like the colors below. I would like the logo to incorporate a home in the design.
Title = Principal-Acquisitions
Email:KRVHOMESOLUTIONS@fernmail.example
555-214-0937
facebook
IG
2 sided business card with the front being contact info a slogan about selling a home fast. The back incorporating What we do. Buy houses, land, or commercial property as is. We find solutions to make the process of selling simple and fair.

Target Market(s)

Motivated house sellers.

Industry/Entity Type

Business

Contact Information for Business Card

Who we are: We are a Faith based Real Estate Investment Company. We pay cash for homes in any condition and can close quick. Whatever the reason you need to sell fast, we can help. We believe in creating win-win solutions to help you in your time of need. We care! We can help!

Logo Text

KRV Home Solutions LLC

Font styles to use
Sans Serif

Colors
33a6d7
0355a3
85abd2
cee9f5
9d9d9d
b2b2b2
ffffff

Requirements
Must have
• Old logo attached. I want something edgier.
• Company name, phone number, description on the back of what we can do. Pay all cash. Buy in as is condition. No fees,Commisions or closing costs.Close quick. No hassles with solutions to meet your unique situation.
• Call today for an offer within 24 hours.

```html
<!DOCTYPE html>
<html lang="en">
<head>
<meta charset="utf-8">
<title>KRV Home Solutions – Business Card</title>
<link rel="stylesheet" href="https://fonts.googleapis.com/css2?family=Roboto:wght@400;500;700&family=Roboto+Condensed:wght@400;700&display=swap">
<style>
  :root {
    --backdrop: #2b2b2b;
    --navy: #1f3566;
    --ink-grey: #555a60;
    --rule-grey: #6b6f74;
    --white: #ffffff;
    --photo-sky: #eef2f2;
    --photo-house: #d9ddd2;
    --photo-lawn: #cfdca8;
  }
  * { box-sizing: border-box; margin: 0; padding: 0; }
  html, body { width: 1200px; height: 960px; overflow: hidden; }
  body {
    background: var(--backdrop);
    position: relative;
    font-family: "Roboto", Arial, sans-serif;
  }
  .card {
    position: absolute;
    width: 600px;
    height: 343px;
    overflow: hidden;
  }
  .card-front { left: 314px; top: 113px; }
  .card-back { left: 311px; top: 472px; background: var(--navy); color: var(--white); text-align: center; }

  .front-photo {
    position: absolute; inset: 0;
    background: linear-gradient(180deg, var(--photo-sky) 0%, var(--photo-house) 45%, var(--photo-lawn) 100%);
  }
  .brand-front {
    position: absolute; right: 34px; top: 100px;
    font-family: "Roboto", Arial, sans-serif;
    font-weight: 700; font-size: 26px; line-height: 1.05;
    color: var(--navy); text-align: center; letter-spacing: 0.5px;
  }
  .brand-front span { display: block; }
  .person-name {
    position: absolute; left: 33px; top: 194px;
    font-family: "Roboto Condensed", Arial, sans-serif;
    font-weight: 700; font-size: 24px; color: var(--navy);
  }
  .person-title {
    position: absolute; left: 33px; top: 222px;
    font-size: 15px; color: var(--ink-grey); font-weight: 500;
  }
  .name-rule {
    position: absolute; left: 33px; top: 249px; width: 285px; height: 2px;
    background: var(--rule-grey);
  }
  .contact-list {
    position: absolute; left: 33px; top: 260px; list-style: none;
    font-size: 15px; color: var(--ink-grey); line-height: 19px;
  }
  .contact-list li { display: flex; align-items: center; gap: 8px; }
  .contact-list svg { width: 13px; height: 13px; fill: var(--navy); flex: none; }
  .selling-points {
    position: absolute; right: 30px; top: 227px; list-style: none;
    font-family: "Roboto Condensed", Arial, sans-serif;
    font-size: 14px; line-height: 18px; color: var(--ink-grey); text-align: right;
  }
  .selling-points li { position: relative; padding-right: 14px; }
  .selling-points li.no-dot { padding-right: 14px; }
  .selling-points li.dot::after {
    content: ""; position: absolute; right: 0; top: 8px;
    width: 4px; height: 4px; border-radius: 50%; background: var(--navy);
  }

  .brand-back {
    position: absolute; left: 0; right: 0; top: 86px;
    font-weight: 700; font-size: 28px; line-height: 1.05; letter-spacing: 0.5px;
  }
  .brand-back span { display: block; }
  .back-heading { font-weight: 700; font-size: 15px; line-height: 18px; }
  .back-copy { font-size: 14.5px; line-height: 18px; }
  .who-we-are { position: absolute; left: 0; right: 0; top: 169px; }
  .what-we-do { position: absolute; left: 0; right: 0; top: 255px; }
  .back-copy { margin-top: 3px; }
</style>
</head>
<body>

<section class="card card-front">
  <div class="front-photo" role="img" aria-label="Faded photograph of a two-storey suburban house with front lawn and garden path"></div>
  <div class="brand-front"><span>KRV HOME</span><span>SOLUTIONS</span></div>
  <h1 class="person-name">MARCUS HALE</h1>
  <p class="person-title">Principal-Acquisitions</p>
  <div class="name-rule"></div>
  <ul class="contact-list">
    <li><svg viewBox="0 0 24 24"><path d="M6.6 10.8a15.1 15.1 0 0 0 6.6 6.6l2.2-2.2c.3-.3.7-.4 1-.2 1.1.4 2.3.6 3.6.6.6 0 1 .4 1 1V20c0 .6-.4 1-1 1A17 17 0 0 1 3 4c0-.6.4-1 1-1h3.5c.6 0 1 .4 1 1 0 1.3.2 2.5.6 3.6.1.3 0 .7-.2 1z"/></svg>555-214-0937</li>
    <li><svg viewBox="0 0 24 24"><path d="M2 5h20v14H2z M2 5l10 7 10-7" /></svg>KRVHOMESOLUTIONS@fernmail.example</li>
    <li><svg viewBox="0 0 24 24"><circle cx="12" cy="12" r="10"/></svg>KRVHOMESOLUTIONS.example</li>
  </ul>
  <ul class="selling-points">
    <li class="dot">Pay all cash. Buy in as is condition</li>
    <li class="dot">No fees,Commisions or closing costs</li>
    <li class="dot">Close quick. No hassles with</li>
    <li class="no-dot">solutions to meet your unique situation</li>
    <li class="dot">Call today for an offer within 24 hours</li>
  </ul>
</section>

<section class="card card-back">
  <div class="brand-back"><span>KRV HOME</span><span>SOLUTIONS</span></div>
  <div class="who-we-are">
    <h2 class="back-heading">WHO WE ARE</h2>
    <p class="back-copy">We are a Faith based Real Estate Investment Company. We pay cash for<br>homes in any condition and can close quick. Whatever the reason you need<br>to sell fast, we can help. We believe in creating win-win solutions to help</p>
  </div>
  <div class="what-we-do">
    <h2 class="back-heading">WHAT WE DO</h2>
    <p class="back-copy">Buy houses, land, or commercial property as is.<br>We find solutions to make the process of selling simple and fair.</p>
  </div>
</section>

</body>
</html>
```